Business Card for Professional Domainer

Require a business card design for an Individual Person who is a Professional Domainer.

Who is a Professional Domainer?
A domainer is someone who earns a profit buying and selling domain names.
Professional Domainer are the ones who do this on a full time basis.

So we require the business card design to be related to the above work.

There is no company or any logo currently, as the card is required for an Individual Person.

Business Card required to mention following details:

1. Full Name of the Person (Ex: Marisol Pike)
2. Education Qualification (Ex: B.Tech Computer Science)
3. Mobile Number (Ex: +71 4837062915)
4. Website (Ex: www.brivolta.example)
5. Email (Ex: contact@brivolta.example)

Positioning of the details:

1. Mobile Number should be placed to Right Top Corner
2. Education Qualification should be just below Full Name
3. Website and Email should be on Bottom Part, on a bar at the bottom

It's important to include images related to the nature of work (Domaining) in the card design.
A good related image would be great. Image should be either in background or as a logo.
The image should be focus of the business card, and shoudl speak out on itself.
Anyone looking at the card should understand at one look what work is being done.
So kindly use images in the design which are highly relevant to domaining and domain names.

Along with the image, it's also good if you use the word "Professional Domainer" anywhere in the design.
Maybe along with the image or somewhere it would fit. These words would be like company name.
So please try to use these words "Professional Domainer" in the design, as it will help a lot.

Colors: Blue, Red, Green

We like these colors, but you are free to use any color which would be good for the design.

Card design should be according to PressaLine specs:

Document Trim Size = 91 x 55 mm | 1075 x 650 pixels
Full Bleed Size = 94 x 58 mm | 1110 x 685 pixels

Last thing, the business card should look professional and clean.
People should know that the person is a Professional Domainer at one look of the card.

Thank You and All the Best :)

Message to the the designers working on this project:

We have now guaranteed this project. This means, we will 100% choose a design and award the project to the one we like the best. So kindly submit your best designs before Wednesday, 3 July 2013. After that we are going to finalize the project and award to the best one. So please hurry up so that you are not too late. Thank You and All the Best!

```html
<!DOCTYPE html>
<html lang="en">
<head>
<meta charset="utf-8">
<title>Marisol Pike – Professional Domainer</title>
<link rel="stylesheet" href="https://fonts.googleapis.com/css2?family=Didact+Gothic&family=Montserrat:wght@700;800&display=swap">
<style>
  :root {
    --teal-deep: #0a2730;
    --teal: #1d6a80;
    --teal-bright: #3a9bb3;
    --suit: #0b0f12;
    --shirt: #d9dcdd;
    --skin: #c9a48e;
    --bar: #4c8197;
    --frame: #4f8aa0;
    --text-light: #ececec;
    --white: #ffffff;
  }
  html, body {
    margin: 0;
    padding: 0;
    overflow: hidden;
    background: #ffffff;
  }
  .card {
    position: relative;
    width: 1200px;
    height: 741px;
    overflow: hidden;
    font-family: "Didact Gothic", sans-serif;
  }
  .card__network {
    position: absolute;
    inset: 0;
    background:
      radial-gradient(ellipse 45% 55% at 72% 28%, var(--teal-bright) 0%, rgba(29,106,128,0.7) 45%, rgba(10,39,48,0) 85%),
      linear-gradient(180deg, var(--teal) 0%, var(--teal-deep) 100%);
  }
  .card__person {
    position: absolute;
    left: 0;
    top: 0;
    width: 640px;
    height: 741px;
    background:
      radial-gradient(ellipse 120px 200px at 75px 300px, var(--shirt) 0%, rgba(217,220,221,0.55) 55%, rgba(217,220,221,0) 100%),
      linear-gradient(90deg, var(--suit) 0%, #12181b 70%, rgba(11,15,18,0) 100%);
  }
  .card__hand {
    position: absolute;
    left: 590px;
    top: 140px;
    width: 260px;
    height: 360px;
    border-radius: 50%;
    background: radial-gradient(ellipse at 50% 45%, rgba(201,164,142,0.85) 0%, rgba(201,164,142,0.35) 50%, rgba(201,164,142,0) 75%);
  }
  .card__shapes {
    position: absolute;
    inset: 0;
  }
  .rotated {
    position: absolute;
    transform-origin: 0 0;
    white-space: nowrap;
    line-height: 1;
  }
  .title {
    left: 585px;
    top: 100px;
    transform: rotate(21deg);
    color: var(--text-light);
    font-size: 90px;
    line-height: 1.05;
  }
  .title__line {
    display: block;
  }
  .title__line--second {
    margin-left: 45px;
  }
  .person-name {
    left: 408px;
    top: 382px;
    transform: rotate(22deg);
    color: var(--white);
    font-family: "Montserrat", sans-serif;
    font-weight: 800;
    font-size: 72px;
    letter-spacing: 3px;
  }
  .qualification {
    left: 374px;
    top: 462px;
    transform: rotate(20deg);
    color: var(--white);
    font-size: 44px;
    letter-spacing: 1px;
  }
  .contact {
    color: var(--white);
  }
  .contact--web {
    left: 64px;
    top: 548px;
    transform: rotate(-71deg);
    font-family: "Montserrat", sans-serif;
    font-weight: 700;
    font-size: 29px;
  }
  .contact--email {
    left: 118px;
    top: 584px;
    transform: rotate(-71deg);
    font-family: "Montserrat", sans-serif;
    font-weight: 700;
    font-size: 27px;
  }
  .contact--phone {
    left: 202px;
    top: 694px;
    transform: rotate(-70deg);
    font-size: 44px;
  }
</style>
</head>
<body>
  <div class="card">
    <div class="card__network" role="img" aria-label="Glowing teal network of white nodes joined by thin lines, standing for linked domain names"></div>
    <div class="card__person" role="img" aria-label="Person in a black suit jacket and white shirt"></div>
    <div class="card__hand" role="img" aria-label="Hand pointing up and touching a glowing network node"></div>

    <svg class="card__shapes" width="1200" height="741" viewBox="0 0 1200 741" aria-hidden="true">
      <polyline class="frame" points="522,20 416,356 1068,574 1190,218"
                fill="none" stroke="var(--frame)" stroke-width="13" stroke-linejoin="miter"/>
      <polygon class="contact-bar" points="232,185 412,243 264,710 62,680" fill="var(--bar)"/>
    </svg>

    <div class="rotated title">
      <span class="title__line">Professional</span>
      <span class="title__line title__line--second">Domainer</span>
    </div>

    <div class="rotated person-name">Marisol Pike</div>
    <div class="rotated qualification">B.Tech Computer Science</div>

    <div class="rotated contact contact--web">www.brivolta.example</div>
    <div class="rotated contact contact--email">contact@brivolta.example</div>
    <div class="rotated contact contact--phone">Ph: +71 4837062915</div>
  </div>
</body>
</html>
```